business card deign

Logo needs the following on it.
1. attached logo
2. Tagline - "If it chills the cooler or lifts the crowd...we bring it!"
3. Name- Dalton Pikes, Founder and CPO
4. Address - 412 E. Carver Avenue, Ste 2207, Tampa, FL. 33917
5. Phone - 555.318.4726

```html
<!DOCTYPE html>
<html lang="en">
<head>
<meta charset="utf-8">
<title>Kavely Business Card</title>
<link rel="stylesheet" href="https://fonts.googleapis.com/css2?family=Montserrat:wght@400;600&display=swap">
<style>
  :root {
    --backdrop: #9d9d9d;
    --card-dark: #1e1e1f;
    --card-light: #ffffff;
    --text-light: #f2f2f2;
    --text-muted: #d8d8d8;
  }
  * { margin: 0; padding: 0; box-sizing: border-box; }
  html, body {
    width: 1093px;
    height: 1200px;
    overflow: hidden;
    background: var(--backdrop);
    font-family: "Montserrat", sans-serif;
  }
  .canvas {
    position: relative;
    width: 1093px;
    height: 1200px;
  }
  .card {
    position: absolute;
    left: 265px;
    width: 580px;
    height: 363px;
    border-radius: 18px;
    background: var(--card-dark);
    overflow: hidden;
  }
  .card--front { top: 225px; }
  .card--back { top: 616px; height: 366px; }

  .front-panel {
    position: absolute;
    inset: 0;
  }
  .holder {
    position: absolute;
    left: 35px;
    top: 43px;
    color: var(--text-light);
  }
  .holder__name {
    font-weight: 600;
    font-size: 20px;
    letter-spacing: 0.2px;
    line-height: 1.1;
  }
  .holder__title {
    font-weight: 400;
    font-size: 12.5px;
    margin-top: 3px;
    color: var(--text-muted);
  }
  .address {
    position: absolute;
    left: 33px;
    top: 200px;
    font-size: 12.5px;
    line-height: 16.5px;
    color: var(--text-light);
  }
  .contacts {
    position: absolute;
    left: 33px;
    top: 256px;
    list-style: none;
    font-size: 12.5px;
    color: var(--text-light);
  }
  .contacts__item {
    display: flex;
    align-items: center;
    height: 17px;
    margin-bottom: 9px;
  }
  .contacts__icon {
    width: 13px;
    height: 13px;
    margin-right: 8px;
    fill: var(--text-light);
  }
  .brand-name {
    position: absolute;
    font-weight: 600;
    text-align: center;
    line-height: 1;
  }
  .brand-name--front {
    left: 340px;
    width: 220px;
    top: 218px;
    font-size: 30px;
    letter-spacing: 13px;
    padding-left: 13px;
    color: var(--card-dark);
  }
  .brand-name--back {
    left: 0;
    width: 580px;
    top: 222px;
    font-size: 44px;
    letter-spacing: 17px;
    padding-left: 17px;
    color: var(--card-light);
  }
  .tagline {
    position: absolute;
    left: 0;
    width: 580px;
    top: 318px;
    text-align: center;
    font-size: 13px;
    color: var(--text-muted);
  }
</style>
</head>
<body>
<main class="canvas">

  <section class="card card--front" aria-label="Card front">
    <svg class="front-panel" width="580" height="363" viewBox="0 0 580 363" aria-hidden="true">
      <path d="M429,0 C350,40 300,120 303,186 C306,255 370,325 432,363 L580,363 L580,0 Z" fill="var(--card-light)"/>
      <path d="M422,4 C346,46 296,124 298,186 C300,254 362,322 424,360" fill="none" stroke="var(--card-light)" stroke-width="1.5"/>
    </svg>

    <div class="holder">
      <h1 class="holder__name">Dalton Pikes</h1>
      <p class="holder__title">Founder and CPO</p>
    </div>

    <p class="address">412 E. Carver Avenue, Ste 2207,<br>Tampa, FL. 33917</p>

    <ul class="contacts">
      <li class="contacts__item">
        <svg class="contacts__icon" viewBox="0 0 24 24" aria-hidden="true"><path d="M6.6 10.8a15.1 15.1 0 0 0 6.6 6.6l2.2-2.2a1 1 0 0 1 1-.25 11.4 11.4 0 0 0 3.6.57 1 1 0 0 1 1 1V20a1 1 0 0 1-1 1A17 17 0 0 1 3 4a1 1 0 0 1 1-1h3.5a1 1 0 0 1 1 1c0 1.25.2 2.45.57 3.6a1 1 0 0 1-.25 1z"/></svg>
        <span>555.318.4726</span>
      </li>
      <li class="contacts__item">
        <svg class="contacts__icon" viewBox="0 0 24 24" aria-hidden="true"><path d="M2 5h20v14H2z"/><path d="M2 6l10 7 10-7" fill="none" stroke="var(--card-dark)" stroke-width="1.6"/></svg>
        <span>info@kavely.com</span>
      </li>
      <li class="contacts__item">
        <svg class="contacts__icon" viewBox="0 0 24 24" aria-hidden="true"><circle cx="12" cy="12" r="10"/><path d="M2 12h20M12 2c3 3 3 17 0 20M12 2c-3 3-3 17 0 20" fill="none" stroke="var(--card-dark)" stroke-width="1.4"/></svg>
        <span>www.kavely.com</span>
      </li>
    </ul>

    <p class="brand-name brand-name--front">KAVELY</p>
  </section>

  <section class="card card--back" aria-label="Card back">
    <p class="brand-name brand-name--back">KAVELY</p>
    <p class="tagline">If it chills the cooler or lifts the crowd...we bring it</p>
  </section>

</main>
</body>
</html>
```